Vosley Insurance Stationery Design Project

We need a stationery design for business cards, letterhead and envelopes.

Please refer to attached brief for further information.

Industry/Entity Type

Business

```html
<!DOCTYPE html>
<html lang="en">
<head>
<meta charset="utf-8">
<title>Vosley Insurance – Business Card</title>
<link rel="stylesheet" href="https://fonts.googleapis.com/css2?family=Questrial&family=Mulish:ital,wght@1,700&display=swap">
<style>
  :root {
    --backdrop: #8a4c02;
    --card-white: #ffffff;
    --navy: #003450;
    --orange: #f47321;
    --band-grey: #e6e6e6;
    --logo-grey: #b4b4b4;
    --ink: #1f3346;
    --divider: #2a2a2a;
    --on-navy: #ffffff;
  }
  * { box-sizing: border-box; margin: 0; padding: 0; }
  html, body { width: 1200px; height: 427px; overflow: hidden; }
  body {
    background: var(--backdrop);
    font-family: "Questrial", "Century Gothic", sans-serif;
    position: relative;
  }
  .card {
    position: absolute;
    top: 77px;
    width: 485px;
    height: 277px;
    border-radius: 25px;
    overflow: hidden;
  }
  .card--front { left: 57px; background: var(--card-white); }
  .card--back { left: 591px; background: var(--navy); color: var(--on-navy); }

  .front__band { position: absolute; left: 0; top: 0; width: 485px; height: 277px; }
  .front__edge {
    position: absolute; top: 0; right: 0; width: 25px; height: 100%;
    background: var(--orange);
    border-left: 2px solid var(--divider);
  }

  .brand {
    position: absolute;
    display: flex; align-items: center; gap: 10px;
    white-space: nowrap;
  }
  .brand__dot {
    width: 22px; height: 22px; border-radius: 50%;
    background: var(--orange); flex: none;
  }
  .brand__name { font-size: 37px; line-height: 1; color: var(--logo-grey); }
  .card--front .brand { left: 90px; top: 46px; }
  .card--back .brand { left: 107px; top: 56px; }
  .card--back .brand__name { font-size: 32px; }

  .tagline {
    position: absolute; left: 0; width: 460px; top: 111px;
    text-align: center;
    font-family: "Mulish", "Open Sans", sans-serif;
    font-style: italic; font-weight: 700;
    font-size: 12.5px; color: var(--orange);
  }
  .holder {
    position: absolute; left: 0; width: 460px; top: 151px;
    text-align: center; color: var(--orange); font-size: 17px;
  }
  .holder__role { font-size: 13px; }
  .address {
    position: absolute; left: 0; width: 460px; top: 188px;
    text-align: center; color: var(--ink); font-size: 12.5px; line-height: 22px;
  }
  .contacts {
    position: absolute; left: 13px; top: 232px;
    display: flex; align-items: center;
    color: var(--ink); font-size: 12.3px; line-height: 18px; letter-spacing: 0.3px;
    white-space: nowrap;
  }
  .contacts__group { padding: 0 9px; border-left: 1px solid var(--ink); }
  .contacts__group:first-child { padding-left: 0; border-left: none; }

  .disclosure {
    position: absolute; left: 0; width: 485px; top: 143px;
    text-align: center; font-size: 11.4px; line-height: 16.3px;
  }
  .back__web {
    position: absolute; left: 0; width: 485px; top: 249px;
    text-align: center; font-size: 13.5px;
  }
</style>
</head>
<body>

<section class="card card--front">
  <svg class="front__band" viewBox="0 0 485 277" aria-hidden="true">
    <path d="M0 222 Q 230 150 485 196 L485 277 L0 277 Z" fill="var(--band-grey)"/>
  </svg>
  <div class="front__edge"></div>

  <div class="brand">
    <span class="brand__dot"></span>
    <span class="brand__name">Vosley Insurance</span>
  </div>

  <p class="tagline">Business and Life Insurance Brokers and Advisers</p>
  <p class="holder">Mark Vosley, <span class="holder__role">Director</span></p>
  <p class="address">PO Box 418., Eastbrook NSW 2071<br>Level 3, 27 Harlow St., Eastbrook NSW 2072</p>

  <div class="contacts">
    <div class="contacts__group">t : (02) 5550 1824</div>
    <div class="contacts__group">m : 0400 555 219<br>f : (02) 5550 1836</div>
    <div class="contacts__group">e : mvosley@norvane.net.au<br>w : www.vosleyinsurance.com.au</div>
  </div>
</section>

<section class="card card--back">
  <div class="brand">
    <span class="brand__dot"></span>
    <span class="brand__name">Vosley Insurance</span>
  </div>
  <p class="disclosure">
    Authorised Representative No. 482913<br>
    Norvane Cover Network Pty Limited AFSL 371065 Insurance<br>
    Norvane Advisory Services Pty Ltd and its advisers are<br>
    members of Harbourline Financial Advisers and Authorised Representatives of<br>
    Tallis Advice Group Pty Ltd AFSL 359184
  </p>
  <p class="back__web">www.vosleyinsurance.com.au</p>
</section>

</body>
</html>
```